Copperleaf Roofing Business Card

This is my current business card. But I’d like to make some changes. Somewhere on the card I’d like to list some of the services we offer. Maybe on the back? But I’d still like to keep the red. White and black modern look.

-residential & commercial roofing
-Roof Repairs & Maintenance
-Storm Damage & Insurance Claims specialist
-Christmas Lights and permanent Christmas lights
Fencing. Windows. Gutters. Siding. Sheetrock, painting.

```html
<!DOCTYPE html>
<html lang="en">
<head>
<meta charset="utf-8">
<title>Copperleaf Roofing Business Card</title>
<link href="https://fonts.googleapis.com/css2?family=Orbitron:wght@800&family=Poppins:wght@400;600;700&display=swap" rel="stylesheet">
<style>
  :root {
    --backdrop: #dfe4e4;
    --card-red: #8f181e;
    --card-red-deep: #7a1217;
    --card-red-mark: #a8191f;
    --card-black: #222226;
    --band-dark: #18181b;
    --accent-red: #e3242b;
    --white: #ffffff;
  }
  * { box-sizing: border-box; margin: 0; padding: 0; }
  html, body { width: 1200px; height: 960px; overflow: hidden; }
  body {
    background: var(--backdrop);
    font-family: "Poppins", sans-serif;
    position: relative;
  }
  .card {
    position: absolute;
    left: 247px;
    width: 706px;
    height: 402px;
    border-radius: 24px;
    overflow: hidden;
    text-align: center;
    color: var(--white);
  }
  .card--services { top: 58px; background: var(--card-red); }
  .card--contact { top: 500px; background: var(--card-black); }

  .brand-mark {
    position: absolute;
    left: 50%;
    border-radius: 50%;
    transform: translateX(-50%);
  }
  .card--services .brand-mark { top: 44px; width: 110px; height: 110px; background: var(--card-red-mark); }
  .card--contact .brand-mark { top: 28px; width: 78px; height: 78px; background: var(--accent-red); }

  .brand-name {
    position: absolute;
    left: 0; right: 0;
    font-family: "Poppins", sans-serif;
    font-weight: 700;
    letter-spacing: 1px;
    line-height: 1.1;
  }
  .card--services .brand-name { top: 164px; font-size: 26px; color: var(--card-red-deep); }
  .card--contact .brand-name { top: 112px; font-size: 17px; color: var(--white); }

  .services {
    position: absolute;
    left: 0; right: 0;
    top: 243px;
    font-size: 16.5px;
    line-height: 23.3px;
  }
  .services__title { font-weight: 700; font-size: 16px; letter-spacing: .5px; margin-bottom: 1px; }
  .services__list { list-style: none; }

  .name-band {
    position: absolute;
    left: 130px; right: 130px;
    top: 182px;
    height: 70px;
    background: linear-gradient(90deg, transparent, var(--band-dark) 20%, var(--band-dark) 80%, transparent);
    box-shadow: 0 -14px 22px -12px rgba(0,0,0,.55), 0 14px 22px -12px rgba(0,0,0,.55);
  }
  .person-name {
    position: absolute;
    left: 0; right: 0;
    top: 188px;
    font-family: "Orbitron", sans-serif;
    font-weight: 800;
    font-size: 29px;
    letter-spacing: 1px;
  }
  .person-name__first { color: var(--accent-red); }
  .person-name__last { color: var(--white); }
  .person-role {
    position: absolute;
    left: 0; right: 0;
    top: 224px;
    font-weight: 600;
    font-size: 17px;
    letter-spacing: .5px;
  }

  .contact-icons {
    position: absolute;
    top: 275px;
    left: 50%;
    transform: translateX(-50%);
    display: flex;
    gap: 5px;
  }
  .contact-icon {
    width: 20px; height: 20px;
    border-radius: 50%;
    background: var(--accent-red);
    display: flex; align-items: center; justify-content: center;
  }
  .contact-details {
    position: absolute;
    left: 0; right: 0;
    top: 306px;
    font-size: 17px;
    line-height: 22.5px;
    letter-spacing: .3px;
    list-style: none;
  }
</style>
</head>
<body>

<section class="card card--services">
  <div class="brand-mark"></div>
  <div class="brand-name">COPPERLEAF<br>ROOFING CO.</div>
  <div class="services">
    <h2 class="services__title">SERVICES WE OFFER</h2>
    <ul class="services__list">
      <li>Roof Repairs &amp; Maintenance</li>
      <li>Residential &amp; Commercial Roofing</li>
      <li>Storm Damage &amp; Insurance Claims Specialist</li>
      <li>Christmas Lights and Permanent Christmas lights</li>
      <li>Fencing. Windows. Gutters. Siding. Sheetrock, Painting</li>
    </ul>
  </div>
</section>

<section class="card card--contact">
  <div class="brand-mark"></div>
  <div class="brand-name">COPPERLEAF<br>ROOFING CO.</div>
  <div class="name-band"></div>
  <h1 class="person-name"><span class="person-name__first">DEAN</span> <span class="person-name__last">MARSH</span></h1>
  <p class="person-role">OWNER</p>

  <div class="contact-icons">
    <span class="contact-icon">
      <svg width="12" height="12" viewBox="0 0 24 24" aria-label="Phone"><path fill="#fff" d="M6.6 10.8a15 15 0 0 0 6.6 6.6l2.2-2.2c.3-.3.7-.4 1-.2 1.1.4 2.3.6 3.6.6.6 0 1 .4 1 1V20c0 .6-.4 1-1 1A17 17 0 0 1 3 4c0-.6.4-1 1-1h3.5c.6 0 1 .4 1 1 0 1.3.2 2.5.6 3.6.1.3 0 .7-.2 1z"/></svg>
    </span>
    <span class="contact-icon">
      <svg width="12" height="12" viewBox="0 0 24 24" aria-label="Email"><rect x="2" y="5" width="20" height="14" rx="2" fill="#fff"/><path d="M3 6l9 7 9-7" fill="none" stroke="#e3242b" stroke-width="2"/></svg>
    </span>
    <span class="contact-icon">
      <svg width="12" height="12" viewBox="0 0 24 24" aria-label="Website"><circle cx="12" cy="12" r="9" fill="none" stroke="#fff" stroke-width="2"/><ellipse cx="12" cy="12" rx="4" ry="9" fill="none" stroke="#fff" stroke-width="2"/><path d="M3 12h18" stroke="#fff" stroke-width="2"/></svg>
    </span>
  </div>

  <ul class="contact-details">
    <li>682-555-0148</li>
    <li>www.copperleafroofing.co</li>
    <li>dean@copperleafroofing.co</li>
  </ul>
</section>

</body>
</html>
```